Profesional personal website needs design and business card

I need a business card with my professional name as a logo "Dorian Vitality" for my business. I am a Wellness Coach, consultant and trainer. So it should be professional, wellness oriented and modern.

Target Market(s)

Private clients, governments, corporations. Luxury and high market.

Industry/Entity Type

Health And Wellness

Contact Information for Business Card

Dorian Vitality should be the logo

Colors

Designer to choose colors to be used in the design.

Requirements
Must have
• Dorian Vitality
• Name: Tomás Lirandel
• Wellness Coach, Consultant & Trainer.
• Website: www.dorianvitality-example.com
• Phone:
• Spain (+34) 612 480 317
• (USA) +1 (555) 610 4829
Nice to have
• The most important is the design of "Dorian Vitality", as this is going to be my personal brand logo. It should be professional, wellness, high end and actual.
Should not have
• no golds, no baroque style..

```html
<!DOCTYPE html>
<html lang="en">
<head>
<meta charset="utf-8">
<title>Dorian Vitality – Business Card</title>
<link href="https://fonts.googleapis.com/css2?family=Bebas+Neue&family=Oswald:wght@400;500&display=swap" rel="stylesheet">
<style>
  :root {
    --backdrop: #2a2a2a;
    --card-white: #ffffff;
    --brand-green: #72ad0e;
    --ink-dark: #3a3a3a;
    --disc-dark: #3d3d3d;
    --rule-grey: #d6d6d6;
  }
  html, body {
    margin: 0;
    padding: 0;
    width: 1200px;
    height: 1200px;
    overflow: hidden;
    background: var(--backdrop);
  }
  .canvas {
    position: relative;
    width: 1200px;
    height: 1200px;
  }
  .card {
    position: absolute;
    top: 310px;
    width: 364px;
    height: 594px;
  }
  .card-front {
    left: 234px;
    background: var(--card-white);
    text-align: center;
  }
  .card-back {
    left: 627px;
    width: 369px;
    background: var(--brand-green);
  }
  .brand-ring {
    position: absolute;
    left: 107px;
    top: 103px;
    width: 122px;
    height: 122px;
    border: 5px solid var(--brand-green);
    border-radius: 50%;
  }
  .brand-name {
    position: absolute;
    left: 0;
    right: 0;
    top: 243px;
    margin: 0;
    font-family: "Bebas Neue", sans-serif;
    font-weight: 400;
    font-size: 48px;
    line-height: 1;
    color: var(--ink-dark);
    letter-spacing: 0.5px;
  }
  .person {
    position: absolute;
    left: 0;
    right: 0;
    top: 372px;
  }
  .person-name {
    margin: 0;
    font-family: "Oswald", sans-serif;
    font-weight: 500;
    font-size: 25px;
    line-height: 1.1;
    color: var(--brand-green);
    text-transform: uppercase;
  }
  .person-role {
    margin: 4px 0 0;
    font-family: "Oswald", sans-serif;
    font-weight: 400;
    font-size: 17px;
    line-height: 1.2;
    color: var(--ink-dark);
    text-transform: uppercase;
  }
  .divider {
    width: 225px;
    height: 1px;
    margin: 12px auto 18px;
    background: var(--rule-grey);
    border: 0;
  }
  .contact {
    margin: 0;
    padding: 0;
    list-style: none;
    font-family: "Oswald", sans-serif;
    font-weight: 400;
    font-size: 17px;
    line-height: 27px;
    color: var(--ink-dark);
    text-transform: uppercase;
  }
  .accent { color: var(--brand-green); }
  .brand-disc {
    position: absolute;
    left: 14px;
    top: 127px;
    width: 340px;
    height: 340px;
    border-radius: 50%;
    background: var(--disc-dark);
    display: flex;
    align-items: center;
    justify-content: center;
    text-align: center;
  }
  .brand-disc-name {
    margin: 0;
    font-family: "Bebas Neue", sans-serif;
    font-weight: 400;
    font-size: 62px;
    line-height: 0.95;
    color: var(--brand-green);
    letter-spacing: 1px;
  }
</style>
</head>
<body>
<main class="canvas">
  <section class="card card-front" aria-label="Business card front">
    <div class="brand-ring"></div>
    <h1 class="brand-name">DORIAN VITALITY</h1>
    <div class="person">
      <p class="person-name">Tomás Lirandel</p>
      <p class="person-role">Wellness Coach, Consultant &amp; Trainer</p>
      <hr class="divider">
      <ul class="contact">
        <li>(+34) 612 480 317 <span class="accent">(Spain)</span></li>
        <li>+1 (555) 610 4829 <span class="accent">(USA)</span></li>
        <li>www.<span class="accent">dorianvitality-example</span>.com</li>
      </ul>
    </div>
  </section>

  <section class="card card-back" aria-label="Business card back">
    <div class="brand-disc">
      <p class="brand-disc-name">DORIAN<br>VITALITY</p>
    </div>
  </section>
</main>
</body>
</html>
```